Website design for an Italian restaurant in Amsterdam

I need a design for a client of mine. It is for Teatro Lucerna, an Italian restaurant in Amsterdam.
We are going for a clean, modern look but we also need to realise an authentic feel.
The restaurant is located in an old movie theatre, that is where the name Teatro Lucerna comes from.
Industry/Entity Type
Italian Restaurant
Number of Pages Required
1 page
Font styles to use
Sans Serif
Colors
Designer to choose colors to be used in the design.

```html
<!DOCTYPE html>
<html lang="en">
<head>
<meta charset="utf-8">
<title>Teatro Lucerna – Ristorante Italiano</title>
<link href="https://fonts.googleapis.com/css2?family=Roboto:wght@300;400;500;700&family=Libre+Baskerville:wght@400;700&family=Great+Vibes&display=swap" rel="stylesheet">
<style>
:root{
  --tan:#a88f70;
  --tan-dark:#957c5d;
  --gold:#e4b81f;
  --ink:#333;
  --muted:#999;
  --red:#b0243a;
  --cream:#efe6dc;
  --paper:#f4f2ef;
  --line:#ddd;
  --white:#fff;
}
*{margin:0;padding:0;box-sizing:border-box}
html,body{width:1200px;height:3103px;overflow:hidden}
body{position:relative;background:var(--white);font-family:"Roboto",Arial,sans-serif;color:var(--ink)}
.abs{position:absolute}

/* header */
.site-header{position:absolute;left:0;top:0;width:1200px;height:93px;background:var(--white)}
.brand-dot{left:172px;top:28px;width:34px;height:34px;border-radius:50%;background:var(--red)}
.brand-name{left:216px;top:32px;font:700 16px "Libre Baskerville",Georgia,serif;color:#222;letter-spacing:.5px}
.brand-tag{left:246px;top:54px;font:400 8px "Roboto",sans-serif;color:var(--red);letter-spacing:1px}
.nav{left:435px;top:0;height:93px;display:flex;font-size:10px;letter-spacing:.5px;color:#555}
.nav span{display:block;height:93px;line-height:93px;padding:0 20px}
.nav .active{background:#f1f1f1;color:#333}
.hours{left:994px;top:29px;font-size:9px;color:#888}
.phone{left:913px;top:46px;font-size:18px;color:#444}

/* hero */
.hero{left:0;top:93px;width:1200px;height:497px;background:radial-gradient(ellipse at 30% 20%,#e0a850 0%,#8a5a2a 30%,#4a3020 65%,#2c1f16 100%)}
.hero-shade{left:0;top:93px;width:1200px;height:497px;background:rgba(70,45,20,.25)}
.hero-rule{height:1px;background:rgba(255,255,255,.8);width:110px}
.hero-script{left:0;width:1200px;top:262px;text-align:center;font:400 66px "Great Vibes",cursive;color:var(--white)}
.hero-title{left:0;width:1200px;top:352px;text-align:center;font:400 44px "Libre Baskerville",Georgia,serif;color:var(--white);letter-spacing:1px}
.hero-sub{left:450px;width:300px;top:416px;text-align:center;font:300 14px/1.3 "Roboto",sans-serif;color:var(--white)}

/* reservation bar */
.reserve-bar{left:0;top:590px;width:1200px;height:74px;background:var(--tan)}
.reserve-head{left:181px;top:603px;color:var(--white);font:700 19px "Roboto",sans-serif;line-height:1}
.reserve-head small{display:block;font:300 15px "Roboto",sans-serif;margin-top:3px}
.reserve-label{top:618px;color:var(--white);font-size:14px}
.field{top:610px;height:35px;background:rgba(255,255,255,.18);color:rgba(255,255,255,.75);font-size:12px;line-height:35px;padding-left:22px}
.btn{background:var(--gold);color:var(--white);font-weight:500;text-align:center}
.reserve-btn{left:920px;top:610px;width:97px;height:35px;line-height:35px;font-size:12px}

/* section titles */
.section-title{left:0;width:1200px;text-align:center;font:400 22px "Libre Baskerville",Georgia,serif;color:#555;letter-spacing:1px}
.title-rule{height:1px;background:#ccc;width:64px}

/* specials grid */
.specials{left:200px;top:828px;width:797px;height:320px;display:grid;grid-template-columns:repeat(5,1fr);grid-template-rows:160px 160px}
.dish{width:100%;height:100%}
.dish-a{background:linear-gradient(135deg,#e3c89a,#8a4a22 60%,#f2efe8)}
.dish-b{background:linear-gradient(135deg,#3b5a7a,#c8502a 55%,#e2c08a)}
.dish-c{background:radial-gradient(circle,#b8301c 0%,#e4ddd0 70%)}
.dish-d{background:linear-gradient(135deg,#e5e0d8,#6a8a3a 40%,#b2422a)}
.dish-e{background:radial-gradient(circle,#d27a3a 0%,#e9d9c0 75%)}
.card{background:#f7f7f7;text-align:center;padding-top:44px}
.card h3{font:400 13px "Roboto",sans-serif;color:#555}
.card i{display:block;width:40px;height:1px;background:#ccc;margin:8px auto 9px}
.card p{font:300 8px/1.4 "Roboto",sans-serif;color:#999;padding:0 22px}

/* sunday banner */
.sunday{left:200px;top:1231px;width:797px;height:221px}
.sunday-kicker{left:222px;top:1244px;font:300 33px "Roboto",sans-serif;color:var(--white)}
.sunday-big{left:222px;top:1282px;font:700 37px "Roboto",sans-serif;color:var(--white)}
.sunday-hours{top:1364px;font:300 12px/1.3 "Roboto",sans-serif;color:var(--white)}
.sunday-btn{left:508px;top:1362px;width:169px;height:34px;line-height:34px;font-size:13px}

/* menu */
.menu-section{left:0;top:1533px;width:1200px;height:608px;background:var(--paper)}
.produce{left:0;top:1533px;width:270px;height:608px;background:linear-gradient(160deg,#d6401e 0%,#e9c25a 22%,#4e8a2c 45%,#eee7da 70%,var(--paper) 100%)}
.tabs{top:1680px;font-size:12px;color:#777}
.tab-active{border:1px solid #bbb;border-radius:3px;padding:5px 16px;background:var(--white)}
.categories{left:310px;top:1760px;font-size:12px;color:#444;line-height:42.4px}
.cat-active{left:257px;top:1791px;width:243px;height:42px;background:rgba(215,215,215,.6)}
.menu-panel{left:500px;top:1742px;width:441px;height:317px;background:rgba(228,228,228,.75);border-radius:4px}
.item{left:522px;width:400px}
.item h4{font:500 12px "Roboto",sans-serif;color:#444}
.item p{font:300 9px/1.4 "Roboto",sans-serif;color:#888;width:270px;margin-top:3px}
.item b{position:absolute;left:335px;top:0;font:400 12px "Roboto",sans-serif;color:#444}

/* testimonials */
.testimonials{left:0;top:2141px;width:1200px;height:290px;background:var(--cream)}
.avatar{border-radius:50%;background:linear-gradient(#d7cfc6,#b9aea2)}
.avatar-main{border:4px solid var(--white);background:linear-gradient(#efe9e2,#c8b6a6)}
.arrow{width:28px;height:28px;border-radius:50%;background:#bdb5ad}
.quote-head{left:438px;top:2238px;font:700 13px "Libre Baskerville",Georgia,serif;color:#333}
.quote-body{left:438px;top:2262px;width:515px;font:400 9px/1.6 "Libre Baskerville",Georgia,serif;color:#666}
.quote-author{left:600px;width:95px;top:2309px;text-align:right;font:700 9px "Libre Baskerville",Georgia,serif;color:#555}
.stars{left:705px;top:2307px;width:100px;height:14px;border-radius:7px;background:var(--gold)}
.dots i{position:absolute;top:2380px;height:4px}

/* contact */
.contact-title{left:209px;top:2512px;font:400 22px "Libre Baskerville",Georgia,serif;color:#555}
.input{left:209px;width:395px;background:#f2f2f2;font-size:9px;color:#aaa;padding:4px 12px}
.send-btn{left:525px;top:2770px;width:79px;height:21px;line-height:21px;font-size:9px}
.social-widget{left:699px;top:2485px;width:313px;height:350px;border:1px solid #e2e2e2;background:var(--white)}
.w-cover{left:700px;top:2486px;width:311px;height:72px;background:linear-gradient(90deg,#1f2a3a,#3a3a4a 60%,#2a2a30)}
.w-thumb{left:712px;top:2512px;width:34px;height:34px;background:#222;border:2px solid var(--white)}
.w-name{left:756px;top:2518px;font:500 12px "Roboto",sans-serif;color:var(--white)}
.w-text{left:712px;top:2570px;font:400 8px/1.45 "Roboto",sans-serif;color:#555}
.w-photo{left:700px;top:2642px;width:311px;height:150px;background:radial-gradient(ellipse at 35% 50%,#8a4a2a 0%,#c99a5a 30%,#f2efe8 65%)}
.w-meta{left:712px;top:2800px;font-size:7px;color:#999}
.w-actions{left:712px;top:2818px;width:290px;display:flex;justify-content:space-between;font-size:7px;color:#999}

/* footer */
.site-footer{left:0;top:2882px;width:1200px;height:190px;background:var(--tan)}
.foot-name{left:118px;width:400px;top:2959px;text-align:center;font:400 19px "Libre Baskerville",Georgia,serif;color:var(--white);letter-spacing:1px}
.foot-tag{left:118px;width:400px;top:2986px;text-align:center;font-size:9px;color:var(--white);letter-spacing:1px}
.foot-addr{left:118px;width:400px;top:3006px;text-align:center;font:400 10px/1.9 "Roboto",sans-serif;color:var(--white)}
.social{top:2975px;width:16px;height:16px;border-radius:50%;background:var(--white)}
.foot-links{left:634px;top:3007px;font-size:10px;color:var(--white);word-spacing:2px}
.copyright{left:0;top:3072px;width:1200px;height:31px;background:var(--tan-dark);border-top:1px solid rgba(255,255,255,.35);text-align:center;line-height:30px;font-size:8px;color:var(--white)}
</style>
</head>
<body>

<header class="site-header">
  <div class="abs brand-dot"></div>
  <div class="abs brand-name">TEATRO LUCERNA</div>
  <div class="abs brand-tag">Ristorante Italiano</div>
  <nav class="abs nav"><span class="active">HOME</span><span>MENU</span><span>GROUP MENU</span><span>RESERVATION</span><span>CONTACT</span></nav>
  <div class="abs hours">&#9719; 18:00 - 23:00</div>
  <div class="abs phone">(+31) 20 555 0184</div>
</header>

<section>
  <div class="abs hero" role="img" aria-label="Warm-lit restaurant dining room with a ring of ceiling lights and set tables"></div>
  <div class="abs hero-shade"></div>
  <div class="abs hero-rule" style="left:545px;top:238px"></div>
  <div class="abs hero-script">Welcome to</div>
  <div class="abs hero-title">TEATRO LUCERNA</div>
  <div class="abs hero-sub">The Italian restaurant located in the heart of Amsterdam</div>
  <div class="abs hero-rule" style="left:545px;top:485px"></div>
</section>

<section>
  <div class="abs reserve-bar"></div>
  <div class="abs reserve-head">RESERVE<small>YOUR TABLE</small></div>
  <svg class="abs" style="left:296px;top:590px" width="14" height="74"><polyline points="2,0 12,37 2,74" fill="none" stroke="#fff" stroke-width="1.5"/></svg>
  <div class="abs reserve-label" style="left:346px">Guests</div>
  <div class="abs field" style="left:415px;width:160px">no. of guests</div>
  <div class="abs reserve-label" style="left:607px">When</div>
  <div class="abs field" style="left:660px;width:235px">select date</div>
  <div class="abs btn reserve-btn">RESERVE</div>
</section>

<section>
  <h2 class="abs section-title" style="top:730px">MONTHLY SPECIAL</h2>
  <div class="abs title-rule" style="left:568px;top:773px"></div>
  <div class="abs specials">
    <div class="dish dish-a" role="img" aria-label="Pasta with braised meat"></div>
    <div class="card"><h3>LOREM IPSUM</h3><i></i><p>Lorem ipsum dolor sit amet, consectetur adipiscing elit. Nunc at.</p></div>
    <div class="dish dish-b" role="img" aria-label="Seafood linguine"></div>
    <div class="card"><h3>LOREM IPSUM</h3><i></i><p>Lorem ipsum dolor sit amet, consectetur adipiscing elit. Nunc at.</p></div>
    <div class="dish dish-c" role="img" aria-label="Spaghetti with meatballs"></div>
    <div class="card"><h3>LOREM IPSUM</h3><i></i><p>Lorem ipsum dolor sit amet, consectetur adipiscing elit. Nunc at.</p></div>
    <div class="dish dish-d" role="img" aria-label="Sliced beef with salad"></div>
    <div class="card"><h3>LOREM IPSUM</h3><i></i><p>Lorem ipsum dolor sit amet, consectetur adipiscing elit. Nunc at.</p></div>
    <div class="dish dish-e" role="img" aria-label="Tagliatelle with tomato sauce"></div>
    <div class="card"><h3>LOREM IPSUM</h3><i></i><p>Lorem ipsum dolor sit amet, consectetur adipiscing elit. Nunc at.</p></div>
  </div>
</section>

<section>
  <svg class="abs sunday" viewBox="0 0 797 221" width="797" height="221">
    <defs><linearGradient id="plate" x1="0" y1="0" x2="1" y2="1"><stop offset="0" stop-color="#3a2e26"/><stop offset=".5" stop-color="#d9d2c8"/><stop offset="1" stop-color="#1c1a1a"/></linearGradient></defs>
    <rect width="797" height="221" fill="#a98e6f"/>
    <polygon points="470,0 797,0 797,221 330,221" fill="url(#plate)" role="img" aria-label="Chef plating a dish"/>
    <path d="M400 35 H768 V188 H32 V70" fill="none" stroke="#fff" stroke-width="3"/>
  </svg>
  <div class="abs sunday-kicker">NOW WE'RE OPEN ON</div>
  <div class="abs sunday-big">SUNDAYS</div>
  <div class="abs sunday-hours" style="left:285px">Tue - Sun<br>Mon</div>
  <div class="abs sunday-hours" style="left:380px;text-align:center">18:00 - 23:00<br>Closed</div>
  <div class="abs btn sunday-btn">RESERVE A TABLE</div>
</section>

<section>
  <div class="abs menu-section"></div>
  <div class="abs produce" role="img" aria-label="Fresh vegetables and dry pasta on a white wooden table"></div>
  <h2 class="abs section-title" style="top:1588px">MENU</h2>
  <div class="abs title-rule" style="left:568px;top:1630px"></div>
  <span class="abs tabs tab-active" style="left:390px">Foods</span>
  <span class="abs tabs" style="left:510px;top:1686px">Beverages</span>
  <span class="abs tabs" style="left:637px;top:1686px">Wines</span>
  <span class="abs tabs" style="left:742px;top:1686px">Deserts</span>
  <div class="abs cat-active"></div>
  <div class="abs categories">Le Insalate<br>Antipasti<br>Le Paste<br>Il Pesce<br>La Carne<br>Contorni<br>Dolce</div>
  <div class="abs menu-panel"></div>
  <div class="abs item" style="top:1758px"><h4>Pane Burro e Tapanada</h4><p>Bread, garlic butter and olive tapenade</p><b>€ 4,50</b></div>
  <div class="abs item" style="top:1808px"><h4>Carpaccio di Manzo</h4><p>Thinly sliced tenderloin with a pesto of rocket salad and parmesan cheese</p><b>€ 13,50</b></div>
  <div class="abs item" style="top:1878px"><h4>Carpaccio di Tonno</h4><p>Thinly sliced tuna with red onion, capers and rocket salad</p><b>€ 14,50</b></div>
  <div class="abs item" style="top:1930px"><h4>Vitello Tonnato</h4><p>Thinly sliced veal with tuna sauce and large capers</p><b>€ 14,75</b></div>
  <div class="abs item" style="top:1982px"><h4>Antipasto Italiano</h4><p>San Daniele ham, spianata salami, Italian cheese, marinated vegetables and olives (min. 2 pers.)</p><b>€ 16,00</b></div>
</section>

<section>
  <div class="abs testimonials"></div>
  <div class="abs avatar" style="left:99px;top:2243px;width:75px;height:75px;opacity:.6" role="img" aria-label="Guest portrait"></div>
  <div class="abs arrow" style="left:204px;top:2266px"></div>
  <div class="abs avatar avatar-main" style="left:291px;top:2226px;width:114px;height:114px" role="img" aria-label="Guest portrait"></div>
  <div class="abs quote-head">Lorem ipsum dolor sit amet, consectetur adipiscing elit.</div>
  <div class="abs quote-body">Lorem ipsum dolor sit amet, consectetur adipiscing elit. Proin interdum purus quis suscipit viverra. Etiam ullamcorper leo ac auctor aliquet. Vivamus ac dolor malesuada, viverra libero nec, accumsan ligula.</div>
  <div class="abs quote-author">- Jane Doe</div>
  <div class="abs stars"></div>
  <div class="abs arrow" style="left:970px;top:2266px"></div>
  <div class="abs avatar" style="left:1025px;top:2243px;width:75px;height:75px;opacity:.6" role="img" aria-label="Guest portrait"></div>
  <div class="dots"><i style="left:472px;width:81px;background:var(--gold)"></i><i style="left:558px;width:82px;background:#aaa"></i><i style="left:643px;width:83px;background:#aaa"></i></div>
</section>

<section>
  <h2 class="abs contact-title">CONTACT US</h2>
  <div class="abs input" style="top:2593px;height:19px">Your name</div>
  <div class="abs input" style="top:2621px;height:19px">Email</div>
  <div class="abs input" style="top:2648px;height:114px">Message</div>
  <div class="abs btn send-btn">SEND</div>

  <div class="abs social-widget"></div>
  <div class="abs w-cover" role="img" aria-label="Restaurant dining room at night"></div>
  <div class="abs w-thumb"></div>
  <div class="abs w-name">Teatro Lucerna</div>
  <div class="abs w-text">Teatro Lucerna · 2 hours ago<br><br>Nuovo Teatro Lucerna.<br>New chef, great authentic Italian food.<br>Getting hungry yet?<br>teatrolucerna.info</div>
  <div class="abs w-photo" role="img" aria-label="Plated meat dish with sauce"></div>
  <div class="abs w-meta">24 likes · 3 comments · 1 share</div>
  <div class="abs w-actions"><span>Like</span><span>Comment</span><span>Share</span></div>
</section>

<footer>
  <div class="abs site-footer"></div>
  <div class="abs foot-name">TEATRO LUCERNA</div>
  <div class="abs foot-tag">Ristorante Italiano</div>
  <div class="abs foot-addr">Lindengracht 42, 1015KM Amsterdam<br>Tel nr.: (+31) 20 555 0184</div>
  <div class="abs social" style="left:886px"></div>
  <div class="abs social" style="left:920px"></div>
  <div class="abs social" style="left:954px"></div>
  <div class="abs foot-links">Home &nbsp;:: Menu &nbsp;:: Group Menu &nbsp;:: Reservation &nbsp;:: Blog &nbsp;:: Contact Us</div>
  <div class="abs copyright">Copyright teatrolucerna.info. All Right Reserved.</div>
</footer>

</body>
</html>
```